Webdesign für neue Weinmarke
Zielgruppe
Kelchwandler ist eine neue Weinmarke. Es wird vorerst drei grundlegende Sorten geben: einen Rotwein, einen Weißwein und einen Rosé. Für diese neue Weinmarke wollen wir eine Webseite gestalten, welche die Weine ansprechend darstellt und zusätzlich den Kunden die Möglichkeit gibt, mehr Informationen über den Wein einzuholen. Die Marke Kelchwandler ist auch im Etikett an den Graf von Tressenbach angelehnt. Das Etikett zeigt den Baron, wie er auf einem Weinfass reitet – daher der Name „Kelchwandler“. Die Story, die wir mit dem Wein spielen, ist, dass die besonderen Fähigkeiten des Barons auch auf den Genuss des Kelchwandler zurückzuführen sind.
Die Zielgruppe für den Kelchwandler ist breit gefächert und schließt per se erst mal keine Personengruppe aus. Der Wein soll eher im niedrigeren Preissegment verkauft werden.
Aufgabenstellung
Es soll eine neue Webseite designt werden, die sich im Aufbau an der die Webseite http://www.velgor-example.de/#!/de/unsere-weine/sortiment orientieren kann. Zudem können für die Entwicklung kleine Animationen berücksichtigt werden, die die Seite auflockern. Das Design soll eine responsive Webseite unterstützen. Das Design soll zur Weinmarke Kelchwandler passen von der wir bisher nur das Etikett haben.

```html
<!DOCTYPE html>
<html lang="de">
<head>
<meta charset="utf-8">
<title>Kelchwandler – Unsere Weine</title>
<link href="https://fonts.googleapis.com/css2?family=Oswald:wght@300;400&family=Hind:wght@300;400&display=swap" rel="stylesheet">
<style>
  :root{
    --page:#f8f7f6;
    --band:#93abb8;
    --band-light:#a3b9c5;
    --ink:#2b2f31;
    --ink-soft:#33393c;
    --map:#2a2c2d;
    --red-top:#2a171b;
    --red-bottom:#4a2a32;
    --white-top:#6f6a3a;
    --white-bottom:#c2b54a;
    --rose-top:#7a2a30;
    --rose-bottom:#d83a48;
  }
  *{box-sizing:border-box;margin:0;padding:0}
  html,body{width:1200px;height:1026px;overflow:hidden;background:var(--page)}
  body{position:relative;font-family:"Hind",sans-serif;color:var(--ink)}
  .wine{position:absolute;left:0;width:1200px;height:192px}
  .wine-band{position:absolute;inset:0;background:linear-gradient(100deg,var(--band) 0%,var(--band-light) 35%,var(--band) 60%,var(--band-light) 85%,var(--band) 100%)}
  .band-edge{position:absolute;left:0;width:1200px;height:8px}
  .band-edge.top{top:-6px}
  .band-edge.bottom{bottom:-7px}
  .bottle-photo{position:absolute;left:256px;top:-19px;width:52px;height:231px;border-radius:4px}
  .bottle-photo.red{background:linear-gradient(180deg,var(--red-top),var(--red-bottom))}
  .bottle-photo.white{background:linear-gradient(180deg,var(--white-top),var(--white-bottom))}
  .bottle-photo.rose{background:linear-gradient(180deg,var(--rose-top),var(--rose-bottom))}
  .wine-title{position:absolute;left:331px;top:16px;font-family:"Oswald",sans-serif;font-weight:400;font-size:17px;line-height:22px;color:var(--ink);transform:scaleX(.86);transform-origin:left;white-space:nowrap}
  .wine-subtitle{position:absolute;left:331px;top:38px;font-family:"Oswald",sans-serif;font-weight:400;font-size:12px;line-height:16px;color:var(--ink);transform:scaleX(.86);transform-origin:left;white-space:nowrap}
  .divider{position:absolute;left:331px;top:60px;width:68px;height:8px}
  .wine-desc{position:absolute;left:331px;top:71px;width:640px;font-weight:300;font-size:9.6px;line-height:13.75px;color:var(--ink-soft);white-space:nowrap}
  .region-map{position:absolute;left:331px;top:114px;width:42px;height:57px}
  .region-text{position:absolute;left:380px;top:116px;width:440px;font-weight:300;font-size:9.6px;line-height:13.75px;color:var(--ink-soft);white-space:nowrap}
  .details{position:absolute;left:884px;top:137px;font-weight:300;font-size:12.5px;line-height:16px;color:var(--ink);text-decoration:none;display:flex;align-items:center;gap:10px}
  .details svg{width:6px;height:8px}
  .wine-nav{position:absolute;right:11px;top:68px;list-style:none}
  .wine-nav li{height:18.75px;display:flex;align-items:center;justify-content:flex-end;gap:5px;font-family:"Oswald",sans-serif;font-weight:300;font-size:10px;color:var(--ink);white-space:nowrap}
  .dot{width:8px;height:8px;border:1.5px solid var(--ink);border-radius:50%;display:flex;align-items:center;justify-content:center}
  .dot.active::after{content:"";width:3px;height:3px;border-radius:50%;background:var(--ink)}
</style>
</head>
<body>

<svg width="0" height="0" style="position:absolute">
  <defs>
    <symbol id="edge-top" viewBox="0 0 1200 8" preserveAspectRatio="none"><path d="M0 8 L520 8 C545 8 560 2 578 2 C590 2 594 5 600 5 C606 5 610 2 622 2 C640 2 655 8 680 8 L1200 8 Z" fill="#93abb8"/></symbol>
    <symbol id="edge-bottom" viewBox="0 0 1200 8" preserveAspectRatio="none"><path d="M0 0 L540 0 C565 0 580 5 592 6 L599 7 L600 8 L601 7 L608 6 C620 5 635 0 660 0 L1200 0 Z" fill="#93abb8"/></symbol>
  </defs>
</svg>

<section class="wine" style="top:89px">
  <div class="wine-band"></div>
  <svg class="band-edge top"><use href="#edge-top"/></svg>
  <svg class="band-edge bottom"><use href="#edge-bottom"/></svg>
  <div class="bottle-photo red" role="img" aria-label="Produktfoto der Rotweinflasche Dornfelder halbtrocken"></div>
  <h2 class="wine-title">Kelchwandler Rotwein</h2>
  <h3 class="wine-subtitle">Kelchwandler Pfälzer Dornfelder</h3>
  <svg class="divider" viewBox="0 0 68 8"><path d="M0 1 L5 4 L0 7 Z" fill="var(--ink)"/><line x1="3" y1="4" x2="62" y2="4" stroke="var(--ink)" stroke-width="1.4"/><path d="M68 4 L62 1 L62 7 Z" fill="var(--ink)"/></svg>
  <p class="wine-desc">Muster Kurze Beschreibung Lorem ipsum dolor sit amet, consetetur sadipscing elitr, sed diam nonumy eirmod tempor invidunt vero eos et accusam<br>et justo labore et dolore magna aliquyam erat, sed diam voluptua. At vero takimata sanctus esteos et accusam et justo duo dolores et ea rebum.</p>
  <svg class="region-map" viewBox="0 0 42 57" role="img" aria-label="Karte von Deutschland mit Markierung der Pfalz">
    <rect width="42" height="57" rx="10" fill="var(--map)"/>
    <path d="M7 30 C7 27 9 25 11 25 C13 25 15 27 15 30 C15 33 11 37 11 37 C11 37 7 33 7 30 Z" fill="#fff"/><circle cx="11" cy="30" r="1.3" fill="var(--map)"/>
  </svg>
  <p class="region-text">Des Kelchwandlers Rot- sowie Weißwein kommen aus dem zweitgrößten deutschen Weinanbaugebiet,<br>der Pfalz. Das einzigartige Klima dieser Region bringt gehaltvolle und wertige Weine hervor. Die Pfalz<br>ist Deutschlands größtes Rotweingebiet und beheimatet zudem auch des Kelchwandlers feinherben<br>Riesling.</p>
  <a class="details" href="#">Details <svg viewBox="0 0 6 8"><path d="M1 1 L4.5 4 L1 7" fill="none" stroke="var(--ink)" stroke-width="1.6"/></svg></a>
  <ul class="wine-nav">
    <li><span>Kelchwandler Rotwein</span><span class="dot active"></span></li>
    <li><span class="dot"></span></li>
    <li><span class="dot"></span></li>
  </ul>
</section>

<section class="wine" style="top:414px">
  <div class="wine-band"></div>
  <svg class="band-edge top"><use href="#edge-top"/></svg>
  <svg class="band-edge bottom"><use href="#edge-bottom"/></svg>
  <div class="bottle-photo white" role="img" aria-label="Produktfoto der Weißweinflasche Riesling feinherb"></div>
  <h2 class="wine-title">Kelchwandler Weißwein</h2>
  <h3 class="wine-subtitle">Kelchwandler Pfälzer Riesling</h3>
  <svg class="divider" viewBox="0 0 68 8"><path d="M0 1 L5 4 L0 7 Z" fill="var(--ink)"/><line x1="3" y1="4" x2="62" y2="4" stroke="var(--ink)" stroke-width="1.4"/><path d="M68 4 L62 1 L62 7 Z" fill="var(--ink)"/></svg>
  <p class="wine-desc">Muster Kurze Beschreibung Lorem ipsum dolor sit amet, consetetur sadipscing elitr, sed diam nonumy eirmod tempor invidunt vero eos et accusam<br>et justo labore et dolore magna aliquyam erat, sed diam voluptua. At vero takimata sanctus esteos et accusam et justo duo dolores et ea rebum.</p>
  <svg class="region-map" viewBox="0 0 42 57" role="img" aria-label="Karte von Deutschland mit Markierung der Pfalz">
    <rect width="42" height="57" rx="10" fill="var(--map)"/>
    <path d="M7 30 C7 27 9 25 11 25 C13 25 15 27 15 30 C15 33 11 37 11 37 C11 37 7 33 7 30 Z" fill="#fff"/><circle cx="11" cy="30" r="1.3" fill="var(--map)"/>
  </svg>
  <p class="region-text">Des Kelchwandlers Rot- sowie Weißwein kommen aus dem zweitgrößten deutschen Weinanbaugebiet,<br>der Pfalz. Das einzigartige Klima dieser Region bringt gehaltvolle und wertige Weine hervor. Die Pfalz<br>ist Deutschlands größtes Rotweingebiet und beheimatet zudem auch des Kelchwandlers feinherben<br>Riesling.</p>
  <a class="details" href="#">Details <svg viewBox="0 0 6 8"><path d="M1 1 L4.5 4 L1 7" fill="none" stroke="var(--ink)" stroke-width="1.6"/></svg></a>
  <ul class="wine-nav">
    <li><span class="dot"></span></li>
    <li><span>Kelchwandler Weißwein</span><span class="dot active"></span></li>
    <li><span class="dot"></span></li>
  </ul>
</section>

<section class="wine" style="top:739px">
  <div class="wine-band"></div>
  <svg class="band-edge top"><use href="#edge-top"/></svg>
  <svg class="band-edge bottom"><use href="#edge-bottom"/></svg>
  <div class="bottle-photo rose" role="img" aria-label="Produktfoto der Roséflasche Dornfelder Rosé"></div>
  <h2 class="wine-title">Kelchwandler Rosé</h2>
  <h3 class="wine-subtitle">Kelchwandler lieblicher Rosé</h3>
  <svg class="divider" viewBox="0 0 68 8"><path d="M0 1 L5 4 L0 7 Z" fill="var(--ink)"/><line x1="3" y1="4" x2="62" y2="4" stroke="var(--ink)" stroke-width="1.4"/><path d="M68 4 L62 1 L62 7 Z" fill="var(--ink)"/></svg>
  <p class="wine-desc">Muster Kurze Beschreibung Lorem ipsum dolor sit amet, consetetur sadipscing elitr, sed diam nonumy eirmod tempor invidunt vero eos et accusam<br>et justo labore et dolore magna aliquyam erat, sed diam voluptua. At vero takimata sanctus esteos et accusam et justo duo dolores et ea rebum.</p>
  <svg class="region-map" viewBox="0 0 42 57" role="img" aria-label="Karte von Deutschland mit Markierung der Pfalz">
    <rect width="42" height="57" rx="10" fill="var(--map)"/>
    <path d="M9 29 C9 26 11 24 13 24 C15 24 17 26 17 29 C17 32 13 36 13 36 C13 36 9 32 9 29 Z" fill="#fff"/><circle cx="13" cy="29" r="1.3" fill="var(--map)"/>
  </svg>
  <p class="region-text">Des Kelchwandlers Rot- sowie Weißwein kommen aus dem zweitgrößten deutschen Weinanbaugebiet,<br>der Pfalz. Das einzigartige Klima dieser Region bringt gehaltvolle und wertige Weine hervor. Die Pfalz<br>ist Deutschlands größtes Rotweingebiet und beheimatet zudem auch des Kelchwandlers feinherben<br>Riesling.</p>
  <a class="details" href="#">Details <svg viewBox="0 0 6 8"><path d="M1 1 L4.5 4 L1 7" fill="none" stroke="var(--ink)" stroke-width="1.6"/></svg></a>
  <ul class="wine-nav">
    <li><span class="dot"></span></li>
    <li><span class="dot"></span></li>
    <li><span>Kelchwandler Rosé</span><span class="dot active"></span></li>
  </ul>
</section>

</body>
</html>
```